Visitenkarten-Design für Yogakurse
Zielgruppe
Ich biete Yogakurse für alle an sowieso speziell Yogakurse für Schwangere, frischgebackene Mamas und Rückbildungskurse.
Meine Zielgruppe sind hauptsächlich schwangere Frauen sowieso Frauen mit Babys.
Aufgabenstellung
Folgende Informationen sollten enthalten sein:
Stille im Atem
Yoga & Beckenbodentraining
Henrike Mollberg
info@stille-im-atem.de
www.stille-im-atem.de

```html
<!DOCTYPE html>
<html lang="de">
<head>
<meta charset="utf-8">
<title>Stille im Atem – Visitenkarte</title>
<link href="https://fonts.googleapis.com/css2?family=Poppins:wght@400;500;700&display=swap" rel="stylesheet">
<style>
  :root {
    --backdrop: #ecebe8;
    --paper: #fbfbf9;
    --gold: #ac8a35;
    --gold-deep: #9c7a2a;
    --ink: #5b5b5b;
    --ink-soft: #3f3f3f;
    --leaf: #a8cb98;
    --white: #ffffff;
  }
  * { box-sizing: border-box; margin: 0; padding: 0; }
  html, body {
    width: 1200px; height: 720px; overflow: hidden;
    background: var(--backdrop);
    font-family: "Poppins", sans-serif;
  }
  .sheet {
    width: 1200px; height: 720px;
    display: flex; align-items: center; justify-content: center; gap: 60px;
  }
  .card {
    width: 520px; height: 336px; border-radius: 4px;
    box-shadow: 0 10px 28px rgba(0,0,0,0.12);
    position: relative;
  }
  /* Front */
  .card--front { background: var(--paper); }
  .brand-mark {
    position: absolute; left: 36px; top: 120px; width: 190px;
    display: flex; flex-direction: column; align-items: center; gap: 14px;
  }
  .brand-mark__dot {
    width: 46px; height: 46px; border-radius: 50%; background: var(--leaf);
  }
  .brand-mark__name {
    font-weight: 500; font-size: 24px; color: var(--gold); text-align: center; line-height: 1.15;
  }
  .details { position: absolute; left: 262px; top: 34px; right: 24px; }
  .details__title { font-weight: 500; font-size: 27px; color: var(--gold); line-height: 1.1; }
  .details__tagline { font-weight: 400; font-size: 14px; color: var(--gold); margin-top: 2px; }
  .details__person { font-weight: 700; font-size: 22px; color: var(--ink); margin-top: 46px; }
  .contact { list-style: none; margin-top: 26px; }
  .contact__item {
    display: flex; align-items: center; gap: 10px;
    font-size: 13px; color: var(--ink-soft); margin-bottom: 9px;
  }
  .contact__icon { width: 16px; height: 16px; flex: none; }
  /* Back */
  .card--back {
    background: linear-gradient(135deg, var(--gold) 0%, var(--gold-deep) 100%);
    display: flex; flex-direction: column; align-items: center; justify-content: center; gap: 18px;
  }
  .card--back .brand-mark__dot { background: var(--white); width: 52px; height: 52px; }
  .card--back .brand-mark__name { color: var(--white); font-size: 30px; }
</style>
</head>
<body>
<main class="sheet">
  <section class="card card--front" aria-label="Vorderseite">
    <div class="brand-mark">
      <span class="brand-mark__dot"></span>
      <span class="brand-mark__name">Stille im Atem</span>
    </div>
    <div class="details">
      <h1 class="details__title">Stille im Atem</h1>
      <p class="details__tagline">Yoga &amp; Beckenbodentraining</p>
      <p class="details__person">Henrike Mollberg</p>
      <ul class="contact">
        <li class="contact__item">
          <svg class="contact__icon" viewBox="0 0 16 16" fill="none" stroke="#3f3f3f" stroke-width="1.3"><path d="M3 2.5h3l1 3-1.6 1.2a8 8 0 0 0 3.9 3.9L10.5 9l3 1v3a1 1 0 0 1-1 1A11 11 0 0 1 2 3.5a1 1 0 0 1 1-1z"/></svg>
          <span>01764829103</span>
        </li>
        <li class="contact__item">
          <svg class="contact__icon" viewBox="0 0 16 16" fill="none" stroke="#3f3f3f" stroke-width="1.3"><rect x="1.5" y="3.5" width="13" height="9" rx="1"/><path d="M1.8 4l6.2 5 6.2-5"/></svg>
          <span>info@stille-im-atem.de</span>
        </li>
        <li class="contact__item">
          <svg class="contact__icon" viewBox="0 0 16 16" fill="none" stroke="#3f3f3f" stroke-width="1.2"><circle cx="8" cy="8" r="6.3"/><ellipse cx="8" cy="8" rx="2.8" ry="6.3"/><path d="M1.7 8h12.6M2.6 5h10.8M2.6 11h10.8"/></svg>
          <span>www.stille-im-atem.de</span>
        </li>
      </ul>
    </div>
  </section>

  <section class="card card--back" aria-label="Rückseite">
    <span class="brand-mark__dot"></span>
    <span class="brand-mark__name">Stille im Atem</span>
  </section>
</main>
</body>
</html>
```